Online media outlet needs a blog and logo

A new online blog platform is being established in the UK. The blog will be very similar in layout to www.quorvel.co. It will need to have a main story slider showing three slides and block tiles beneath the slider for additional tiles.

The blog platform will be called 'Tandrel Brisk' and will also need a professional looking logo design for the name.

The website should be designed in Word Press.

Industry/Entity Type

Media

Logo Text

Tandrel Brisk

Coding

Coded - Design and coding required

Number of Pages Required

3 page

Font styles to use
Other font styles liked:
• Helvetica

Requirements
Must have
• A slider showing three slides. Be similar to Quor V (see previous comment). Be Word Press compatible.

```html
<!DOCTYPE html>
<html lang="en">
<head>
<meta charset="utf-8">
<title>Tandrel Brisk</title>
<link rel="stylesheet" href="https://fonts.googleapis.com/css2?family=Raleway:wght@400;500;600;700&display=swap">
<style>
:root{
  --bar-top:#3aa3d6;
  --bar-bottom:#1b6f9e;
  --accent:#2a86bf;
  --page:#efefef;
  --card:#ffffff;
  --ink:#2b2b2b;
  --muted:#8a8a8a;
  --line:#d9d9d9;
  --footer:#262626;
  --white:#ffffff;
  --star:#f2b01e;
}
*{margin:0;padding:0;box-sizing:border-box}
html,body{width:1200px;height:4276px;overflow:hidden}
body{background:var(--page);font-family:"Raleway",Helvetica,Arial,sans-serif;color:var(--ink);position:relative}
.abs{position:absolute}
.photo{display:block}

/* header */
.topbar{top:0;left:0;width:1200px;height:63px;background:linear-gradient(var(--bar-top),var(--bar-bottom));display:flex;align-items:center;justify-content:space-between;padding:0 100px}
.brand{color:var(--white);font-size:26px;font-weight:600;letter-spacing:.5px}
.top-tools{display:flex;gap:10px;align-items:center}
.circle-btn{width:36px;height:36px;border:2px solid var(--white);border-radius:50%}
.search-btn{width:50px;height:40px;margin-left:20px;background:rgba(255,255,255,.15);display:flex;align-items:center;justify-content:center}

.hero{top:63px;left:0;width:1200px;height:385px;background:linear-gradient(180deg,#1d3550 0%,#2e4c6b 45%,#243241 70%,#14181d 100%)}
.hero-nav{top:102px;left:160px;width:880px;height:46px;border-top:1px solid rgba(255,255,255,.4);border-bottom:1px solid rgba(255,255,255,.4);display:flex;justify-content:space-around;align-items:center;color:var(--white);font-size:14px}
.hero-title{top:262px;left:0;width:1200px;text-align:center;color:var(--white);font-size:42px;font-weight:500}
.hero-arrow{top:240px;color:var(--white);font-size:30px}

/* tiles */
.tile{overflow:hidden;box-shadow:0 2px 6px rgba(0,0,0,.2)}
.tile .photo{position:absolute;inset:0}
.tile .shade{position:absolute;inset:0;background:linear-gradient(transparent 45%,rgba(0,0,0,.75))}
.tile h3{position:absolute;left:16px;right:16px;bottom:48px;color:var(--white);font-size:21px;font-weight:500;line-height:1.35}
.tile .meta{position:absolute;left:16px;bottom:16px;color:#ddd;font-size:12px}
.tile .dot{position:absolute;right:14px;bottom:16px;width:14px;height:14px;border-radius:50%;background:var(--white)}

/* section heads */
.sec-head{left:100px;width:997px;display:flex;align-items:center;gap:20px}
.sec-head h2{color:var(--accent);font-size:22px;font-weight:600;white-space:nowrap}
.sec-head .rule{flex:1;height:1px;background:var(--line)}
.sec-head .arrows{color:var(--ink);font-size:18px}

.news-item .photo{height:174px}
.news-item h4{margin-top:18px;font-size:19px;font-weight:500;line-height:1.4}
.news-item .date{margin-top:14px;color:var(--accent);font-size:13px}

/* newsletter */
.newsletter{top:1510px;left:100px;width:997px;height:303px;background:linear-gradient(135deg,#4a3a33,#2e2521 60%,#3b2f2a);color:var(--white);text-align:center}
.newsletter h2{margin-top:50px;font-size:26px;font-weight:500}
.newsletter p{width:800px;margin:26px auto 0;font-size:12px;line-height:1.8;color:#e2dad6}
.nl-form{display:flex;justify-content:center;gap:30px;margin-top:34px}
.nl-email{width:340px;height:38px;border-bottom:1px solid rgba(255,255,255,.6);text-align:left;font-size:12px;padding-top:12px}
.nl-btn{width:160px;height:40px;background:var(--white);color:var(--accent);font-size:16px;font-weight:600;display:flex;align-items:center;justify-content:center}

/* posts */
.card{background:var(--card);box-shadow:0 1px 4px rgba(0,0,0,.12)}
.post{padding:14px 14px 0}
.post .photo{height:214px}
.post-meta{display:flex;gap:40px;margin:28px 0 0 10px;font-size:13px;color:var(--muted)}
.post-meta b{color:var(--accent);font-weight:400}
.post h3{margin:22px 0 0 10px;font-size:21px;font-weight:500}
.post p{margin:16px 10px 0;font-size:12px;line-height:1.7;color:var(--muted)}
.read{margin:10px 10px 0;text-align:right;font-size:12px;color:var(--accent)}
.small-post{padding:8px}
.small-post .photo{height:180px}
.small-post .post-meta{gap:16px;margin:22px 0 0 6px;font-size:12px}
.small-post h3{margin:16px 0 0 6px;font-size:17px;font-weight:500}
.small-post p{margin:12px 6px 0;font-size:12px;line-height:1.6;color:var(--muted)}
.small-post .read{text-align:left;margin:14px 6px 0}

/* sidebar */
.sidebar{top:1852px;left:798px;width:299px;height:1311px}
.side-head{height:44px;border-bottom:3px solid var(--accent);text-align:center;font-size:16px;font-weight:600;padding-top:12px;color:#3a3a3a}
.feed{padding:0 18px;height:177px;border-bottom:1px solid #eee;padding-top:30px}
.feed-top{display:flex;gap:10px}
.feed .thumb{width:40px;height:40px}
.feed .who{font-size:13px}
.feed .stars{color:var(--star);font-size:11px;margin-top:4px;letter-spacing:1px}
.feed p{margin-top:12px;font-size:11px;line-height:1.6;color:#555}
.feed .acts{display:flex;gap:40px;margin-top:20px;font-size:12px;color:var(--muted)}
.side-foot{padding:22px 18px 0;font-size:12px;color:#666;line-height:1.6}
.side-search{margin-top:10px;height:32px;border:1px solid var(--line);font-size:11px;padding:8px;color:#aaa}

.spinner{top:3945px;left:584px}

/* footer */
.footer{top:4018px;left:0;width:1200px;height:258px;background:var(--footer);color:var(--white)}
.f-icons{display:flex;justify-content:center;gap:22px;margin-top:48px}
.f-icons span{width:54px;height:54px;border:3px solid var(--white);border-radius:50%}
.f-rule{width:260px;height:1px;background:#555;margin:24px auto 0}
.f-nav{display:flex;justify-content:center;gap:34px;margin-top:30px;font-size:13px}
.f-copy{text-align:center;margin-top:22px;font-size:11px;color:#ccc}
</style>
</head>
<body>

<header class="topbar abs">
  <div class="brand">Tandrel Brisk</div>
  <div class="top-tools">
    <span class="circle-btn"></span><span class="circle-btn"></span><span class="circle-btn"></span><span class="circle-btn"></span>
    <span class="search-btn"><svg width="18" height="18" viewBox="0 0 18 18"><circle cx="7.5" cy="7.5" r="5.5" fill="none" stroke="#fff" stroke-width="2"/><line x1="11.5" y1="11.5" x2="16" y2="16" stroke="#fff" stroke-width="2.4"/></svg></span>
  </div>
</header>

<section class="hero abs" role="img" aria-label="Night view of a lit suspension bridge over water with wooden pier posts"></section>
<nav class="hero-nav abs"><span>Home</span><span>About us</span><span>Features</span><span>News</span><span>Contact us</span></nav>
<span class="hero-arrow abs" style="left:50px">‹</span>
<span class="hero-arrow abs" style="left:1130px">›</span>
<h1 class="hero-title abs">Welcome To Tandrel Brisk</h1>

<!-- featured tiles -->
<article class="tile abs" style="top:490px;left:100px;width:320px;height:322px">
  <div class="photo" role="img" aria-label="Businesswoman working at a laptop" style="background:linear-gradient(160deg,#e9e9e9,#bfbfbf 60%,#3a3a3a)"></div>
  <div class="shade"></div><h3>In diam invenire est pri numq corpora intellegat an</h3><div class="meta">Investment · May 3, 2016</div><span class="dot"></span>
</article>
<article class="tile abs" style="top:490px;left:436px;width:320px;height:322px">
  <div class="photo" role="img" aria-label="Speaker presenting to a conference audience" style="background:linear-gradient(160deg,#f0eef0,#c9b9c2 55%,#4a3a40)"></div>
  <div class="shade"></div><h3>In diam invenire est pri numq corpora intellegat an</h3><div class="meta">Government · May 3, 2016</div><span class="dot"></span>
</article>
<article class="tile abs" style="top:490px;left:776px;width:321px;height:322px">
  <div class="photo" role="img" aria-label="Press photographers at an event" style="background:linear-gradient(160deg,#d8c9c6,#9b8b88 55%,#3a3434)"></div>
  <div class="shade"></div><h3>In diam invenire est pri numq corpora intellegat an</h3><div class="meta">Investment · May 3, 2016</div><span class="dot"></span>
</article>
<article class="tile abs" style="top:832px;left:100px;width:488px;height:265px">
  <div class="photo" role="img" aria-label="Business handshake over a table" style="background:linear-gradient(160deg,#8a8a8a,#4a4a4a 60%,#1f1f1f)"></div>
  <div class="shade"></div><h3>Sea at offendit rationibus, ne ceteros comm fastidii nec, an usu quas clita integre</h3><div class="meta">Government · May 3, 2016</div><span class="dot"></span>
</article>
<article class="tile abs" style="top:832px;left:607px;width:490px;height:265px">
  <div class="photo" role="img" aria-label="Guests raising glasses at a reception" style="background:linear-gradient(160deg,#6e6a5e,#3c4030 60%,#161810)"></div>
  <div class="shade"></div><h3>Sea at offendit rationibus, ne ceteros comm fastidii nec, an usu quas clita integre</h3><div class="meta">Investment · May 3, 2016</div><span class="dot"></span>
</article>

<!-- latest news -->
<div class="sec-head abs" style="top:1138px"><h2>Latest News</h2><span class="rule"></span><span class="arrows">‹ ›</span></div>
<article class="news-item abs" style="top:1200px;left:100px;width:235px">
  <div class="photo" role="img" aria-label="Combine harvester in a wheat field" style="background:linear-gradient(#6aa0d8,#9cc0e0 40%,#d4a53a 55%,#b88a2a)"></div>
  <h4>Ex natum facete nostrud velsit lorem oporteat</h4><div class="date">May 3, 2016</div>
</article>
<article class="news-item abs" style="top:1200px;left:354px;width:236px">
  <div class="photo" role="img" aria-label="Close-up of a metal chain" style="background:linear-gradient(135deg,#cfd6dd,#7e8a96 50%,#dfe4e8)"></div>
  <h4>In diam invenire est pri numquam corpora</h4><div class="date">May 3, 2016</div>
</article>
<article class="news-item abs" style="top:1200px;left:610px;width:487px">
  <div class="photo" role="img" aria-label="Cathedral domes and a statue under a blue sky" style="background:linear-gradient(#5f9fd8,#a8cdee 45%,#b5844a 70%,#6e5a3a)"></div>
  <h4>In diam invenire est pri numquam corpora &nbsp;Cum fastidii consequat invenire est</h4><div class="date">May 3, 2016</div>
</article>

<!-- newsletter -->
<section class="newsletter abs" role="img" aria-label="Newsletter signup over a dim photo of a desk with papers">
  <h2>Newsletter Signup</h2>
  <p>In diam invenire est, pri numquam corpora intellegat an. Cum fastidii consequat ut, eam ex lorem falli, ex percipit luptatum intellegam cum. Ex blandit oporteat voluptatibus quo, vix neque decore id, nam ullamcorper aliquam ad. In delenit invidunt vix diam consequat et, eam.</p>
  <div class="nl-form"><div class="nl-email">Email</div><div class="nl-btn">Subscribe</div></div>
</section>

<!-- posts -->
<article class="card post abs" style="top:1852px;left:100px;width:647px;height:442px">
  <div class="photo" role="img" aria-label="Woman speaking into a microphone" style="background:linear-gradient(90deg,#f4f4f4,#d8d8d8 45%,#e8c36a 80%,#f0d88a)"></div>
  <div class="post-meta"><span><b>✎</b> By Blandit Oporteat</span><span><b>▦</b> May 3, 2016</span><span><b>✉</b> By Blandit Oporteat</span></div>
  <h3>In diam invenire est pri numquam corpora</h3>
  <p>Ex natum facete nostrud vel, sit an lorem oporteat. Te possim expetenda contentiones qui, ut melius inimicus dissentiunt ius. Ex blandit oporteat voluptatibus quo, vix neque decore id, nam ullamcorper aliquam ad. In delenit invidunt vix.</p>
  <div class="read">Read More Info »</div>
</article>
<article class="card post abs" style="top:2323px;left:100px;width:647px;height:441px">
  <div class="photo" role="img" aria-label="Close-up of green rice stalks" style="background:linear-gradient(120deg,#cfe07a,#7fa832 50%,#d8d89a)"></div>
  <div class="post-meta"><span><b>✎</b> By Blandit Oporteat</span><span><b>▦</b> May 3, 2016</span><span><b>✉</b> ( 3 ) Comments</span></div>
  <h3>In diam invenire est pri numquam corpora</h3>
  <p>Ex natum facete nostrud vel, sit an lorem oporteat. Te possim expetenda contentiones qui, ut melius inimicus dissentiunt ius. Ex blandit oporteat voluptatibus quo, vix neque decore id, nam ullamcorper aliquam ad. In delenit invidunt vix.</p>
  <div class="read">Read More Info »</div>
</article>
<article class="card small-post abs" style="top:2784px;left:100px;width:311px;height:379px">
  <div class="photo" role="img" aria-label="Colleagues reviewing documents together" style="background:linear-gradient(135deg,#e6d2b8,#8a6a50 55%,#2e2622)"></div>
  <div class="post-meta"><span><b>▦</b> May 3, 2016</span><span><b>✉</b> ( 3 ) Comments</span></div>
  <h3>In diam invenire est pri numquam</h3>
  <p>In diam invenire est, pri numquam corpora intellegat an. Cum fastidii consequat ut eam ex.</p>
  <div class="read">Read More Info »</div>
</article>
<article class="card small-post abs" style="top:2784px;left:436px;width:311px;height:379px">
  <div class="photo" role="img" aria-label="Audience seated at a seminar" style="background:linear-gradient(135deg,#d8d8d8,#7a7a7a 55%,#2a2a2a)"></div>
  <div class="post-meta"><span><b>▦</b> May 3, 2016</span><span><b>✉</b> ( 3 ) Comments</span></div>
  <h3>In diam invenire est pri numquam</h3>
  <p>In diam invenire est, pri numquam corpora intellegat an. Cum fastidii consequat ut eam ex.</p>
  <div class="read">Read More Info »</div>
</article>

<!-- sidebar -->
<aside class="card sidebar abs">
  <div class="side-head">Featured Media News</div>
  <div class="feed"><div class="feed-top"><div class="thumb" role="img" aria-label="Red news thumbnail" style="background:#d9403a"></div><div><div class="who">De Lege@ Docendi</div><div class="stars">★★★★★</div></div></div><p>De doel die plotseling leeg is. De leuning en het dikste alsof het eerder leven.</p><div class="acts"><span>↰</span><span>⟲ 0</span><span>♥ 0</span></div></div>
  <div class="feed"><div class="feed-top"><div class="thumb" role="img" aria-label="Grey news thumbnail" style="background:#6a6a6a"></div><div><div class="who">De Lege@ Docendi</div><div class="stars">★★★★★</div></div></div><p>De doel die plotseling leeg is. De leuning en het dikste alsof het eerder leven.</p><div class="acts"><span>↰</span><span>⟲ 0</span><span>♥ 0</span></div></div>
  <div class="feed"><div class="feed-top"><div class="thumb" role="img" aria-label="Group photo thumbnail" style="background:#b89a84"></div><div><div class="who">De Lege@ <b>Docendi</b></div><div class="stars">★★★★★</div></div></div><p>De doel die plotseling leeg is. De leuning en het dikste alsof het eerder leven.</p><div class="acts"><span>↰</span><span>⟲ 0</span><span>♥ 0</span></div></div>
  <div class="feed"><div class="feed-top"><div class="thumb" role="img" aria-label="Red news thumbnail" style="background:#d9403a"></div><div><div class="who">De Lege@ <b>Docendi</b></div><div class="stars">★★★★★</div></div></div><p>De doel die plotseling leeg is. De leuning en het dikste alsof het eerder leven.</p><div class="acts"><span>↰</span><span>⟲ 0</span><span>♥ 0</span></div></div>
  <div class="feed"><div class="feed-top"><div class="thumb" role="img" aria-label="Grey news thumbnail" style="background:#6a6a6a"></div><div><div class="who">De Lege@ <b>Docendi</b></div><div class="stars">★★★★★</div></div></div><p>De doel die plotseling leeg is. De leuning en het dikste alsof het eerder leven.</p><div class="acts"><span>↰</span><span>⟲ 0</span><span>♥ 0</span></div></div>
  <div class="feed"><div class="feed-top"><div class="thumb" role="img" aria-label="Group photo thumbnail" style="background:#b89a84"></div><div><div class="who">De Lege@ <b>Docendi</b></div><div class="stars">★★★★★</div></div></div><p>De doel die plotseling leeg is. De leuning en het dikste alsof het eerder leven.</p><div class="acts"><span>↰</span><span>⟲ 0</span><span>♥ 0</span></div></div>
  <div class="side-foot">Vix no dicunt intellegat, eirmod adolescens eam no, ven graeco denique vis ad.<div style="margin-top:10px">Search here</div><div class="side-search">Type here</div></div>
</aside>

<!-- best events -->
<div class="sec-head abs" style="top:3196px"><h2>Best Events</h2><span class="rule"></span><span class="arrows">‹ ›</span></div>
<article class="news-item abs" style="top:3257px;left:100px;width:235px">
  <div class="photo" role="img" aria-label="Dancers in bright costumes at a street parade" style="height:177px;background:linear-gradient(135deg,#6fb04a,#e6d23a 45%,#3e7a34)"></div>
  <h4>Ex natum facete nostrud velsit lorem oporteat</h4><div class="date">May 3, 2016</div>
</article>
<article class="news-item abs" style="top:3257px;left:354px;width:236px">
  <div class="photo" role="img" aria-label="Crowd at an outdoor rally" style="height:177px;background:linear-gradient(135deg,#7aa6d8,#d04a4a 50%,#e8e0d0)"></div>
  <h4>In diam invenire est pri numquam corpora</h4><div class="date">May 3, 2016</div>
</article>
<article class="news-item abs" style="top:3257px;left:610px;width:487px">
  <div class="photo" role="img" aria-label="Fresh tomatoes on a dark table" style="height:177px;background:linear-gradient(90deg,#2a2420,#8a2a1e 45%,#c4442a 60%,#2a2420)"></div>
  <h4>In diam invenire est pri numquam corpora &nbsp;Cum fastidii consequat invenire est</h4><div class="date">May 3, 2016</div>
</article>

<article class="tile abs" style="top:3577px;left:100px;width:320px;height:322px">
  <div class="photo" role="img" aria-label="Two colleagues smiling in an office" style="background:linear-gradient(160deg,#c8a060,#7a5a3a 55%,#2a2018)"></div>
  <div class="shade"></div><h3>In diam invenire est pri numq corpora intellegat an</h3><div class="meta">Investment · May 3, 2016</div><span class="dot"></span>
</article>
<article class="tile abs" style="top:3577px;left:436px;width:320px;height:322px">
  <div class="photo" role="img" aria-label="Red brick government building under blue sky" style="background:linear-gradient(#3f78c8,#8ab4e4 40%,#a0553a 65%,#5a3a2a)"></div>
  <div class="shade"></div><h3>In diam invenire est pri numq corpora intellegat an</h3><div class="meta">Government · May 3, 2016</div><span class="dot"></span>
</article>
<article class="tile abs" style="top:3577px;left:776px;width:321px;height:322px">
  <div class="photo" role="img" aria-label="Desert pyramids at sunset" style="background:linear-gradient(#e8b060,#d88a3a 50%,#9a6a3a)"></div>
  <div class="shade"></div><h3>In diam invenire est pri numq corpora intellegat an</h3><div class="meta">Investment · May 3, 2016</div><span class="dot"></span>
</article>

<svg class="spinner abs" width="32" height="32" viewBox="0 0 32 32" aria-hidden="true">
  <g fill="#555"><circle cx="16" cy="3" r="3"/><circle cx="25" cy="7" r="2.7" opacity=".9"/><circle cx="29" cy="16" r="2.4" opacity=".8"/><circle cx="25" cy="25" r="2.1" opacity=".7"/><circle cx="16" cy="29" r="1.9" opacity=".6"/><circle cx="7" cy="25" r="1.7" opacity=".5"/><circle cx="3" cy="16" r="1.5" opacity=".4"/></g>
</svg>

<footer class="footer abs">
  <div class="f-icons"><span></span><span></span><span></span><span></span></div>
  <div class="f-rule"></div>
  <div class="f-nav"><span>Home</span><span>·</span><span>About us</span><span>·</span><span>Features</span><span>·</span><span>News</span><span>·</span><span>Contact us</span></div>
  <div class="f-copy">All Rights Reserved . copyright2016@companyname.com</div>
</footer>

</body>
</html>
```